Harbourline Electrical Solutions

On one side. LOGO (underneath:) Commercial Industrial Residential

- NAME & CONTACT DETAILS

Marcus T. Hollings
Project Manager

(Cell icon) (441) 555-0187
(Email icon) hlelectricalsolutions@mailvento.com
(Facebook & Instagram icons )@hlelectricalsolutions

Other side: LOGO - underneath ELECTRICAL CONSTRUCTION & MAINTENANCE . LED LIGHTING & AUTOMATION . LIFE SAFETY SYSTEMS (FIRE ALARM / SECURITY) . DATA & COMMUNICATION

```html
<!DOCTYPE html>
<html lang="en">
<head>
<meta charset="utf-8">
<title>Harbourline Electrical Solutions – Business Card</title>
<link rel="stylesheet" href="https://fonts.googleapis.com/css2?family=Montserrat:wght@400;500;600;700&display=swap">
<style>
  :root {
    --backdrop: #2a2a2c;
    --slate: #505050;
    --teal: #105569;
    --teal-ink: #134f63;
    --teal-light: #1a6a80;
    --paper: #ffffff;
    --ink: #2f2f2f;
    --muted: #3d3d3d;
  }
  * { margin: 0; padding: 0; box-sizing: border-box; }
  html, body {
    width: 1200px; height: 1200px; overflow: hidden;
    background: var(--backdrop);
    font-family: "Montserrat", sans-serif;
  }
  .card {
    position: absolute; left: 293px;
    width: 614px; height: 368px; overflow: hidden;
  }

  /* Services side */
  .card--services { top: 217px; background: var(--slate); }
  .service-list {
    position: absolute; left: 82px; top: 140px;
    list-style: none; color: #fff;
    font-weight: 600; font-size: 12.6px; line-height: 15px;
  }
  .service-list li {
    position: relative; padding-left: 9px; margin-bottom: 8px;
  }
  .service-list li::before {
    content: ""; position: absolute; left: 0; top: 4px;
    width: 4px; height: 4px; background: #fff;
  }
  .brand-band {
    position: absolute; right: 0; top: 0;
    width: 172px; height: 100%; background: var(--teal);
  }
  .brand-band__name {
    position: absolute; left: 56px; top: 160px;
    transform: rotate(-90deg); transform-origin: left top;
    translate: 0 0;
    color: var(--teal-light);
    font-weight: 500; font-size: 15px; line-height: 18px;
    letter-spacing: 2.6px; white-space: nowrap;
  }

  /* Contact side */
  .card--contact { top: 632px; background: var(--paper); }
  .brand {
    position: absolute; left: 62px; top: 148px;
  }
  .brand__mark-row { display: flex; align-items: center; gap: 10px; }
  .brand__square { width: 30px; height: 30px; background: var(--teal-ink); }
  .brand__name {
    color: var(--teal-ink); font-weight: 500;
    font-size: 12.4px; line-height: 13px; letter-spacing: 2.2px;
  }
  .brand__tagline {
    margin-top: 14px; color: var(--ink);
    font-weight: 500; font-size: 7.6px; letter-spacing: 1.7px;
    white-space: nowrap;
  }
  .brand__tagline .sep { color: var(--teal-ink); margin: 0 4px; }
  .divider {
    position: absolute; left: 295px; top: 132px;
    width: 1px; height: 97px; background: var(--teal-ink);
  }
  .person { position: absolute; left: 309px; top: 131px; }
  .person__name {
    color: var(--teal-ink); font-weight: 700;
    font-size: 16.5px; line-height: 20px; letter-spacing: 0.2px;
  }
  .person__role {
    color: var(--ink); font-weight: 500; font-size: 11.5px; line-height: 14px;
  }
  .contact-list { list-style: none; margin-top: 13px; }
  .contact-list li {
    display: flex; align-items: center; gap: 4px;
    color: var(--muted); font-size: 12.2px; line-height: 19px;
    letter-spacing: 0.3px;
  }
  .icon { width: 12px; height: 12px; flex: none; }
</style>
</head>
<body>

<section class="card card--services" aria-label="Card front: services">
  <ul class="service-list">
    <li>ELECTRICAL CONSTRUCTION<br>&amp; MAINTENANCE</li>
    <li>LED LIGHTING &amp; AUTOMATION</li>
    <li>LIFE SAFETY SYSTEMS<br>(FIRE ALARM / SECURITY)</li>
    <li>DATA &amp; COMMUNICATION</li>
  </ul>
  <div class="brand-band">
    <div class="brand-band__name" style="top:330px;left:60px;">HARBOURLINE<br>ELECTRICAL<br>SOLUTIONS</div>
  </div>
</section>

<section class="card card--contact" aria-label="Card back: contact details">
  <div class="brand">
    <div class="brand__mark-row">
      <span class="brand__square"></span>
      <div class="brand__name">HARBOURLINE<br>ELECTRICAL<br>SOLUTIONS</div>
    </div>
    <div class="brand__tagline">COMMERCIAL<span class="sep">|</span>INDUSTRIAL<span class="sep">|</span>RESIDENTIAL</div>
  </div>

  <div class="divider"></div>

  <div class="person">
    <div class="person__name">MARCUS T. HOLLINGS</div>
    <div class="person__role">Project Manager</div>
    <ul class="contact-list">
      <li>
        <svg class="icon" viewBox="0 0 12 12" aria-hidden="true">
          <circle cx="6" cy="6" r="5.4" fill="none" stroke="var(--teal-ink)" stroke-width="0.9"/>
          <path d="M4 3.3l1 1.1-.5.8c.4.9 1 1.5 1.9 1.9l.8-.5 1.1 1-.6.9c-2 0-3.9-1.9-3.9-3.9z" fill="var(--teal-ink)"/>
        </svg>
        (441) 555-0187
      </li>
      <li>
        <svg class="icon" viewBox="0 0 12 12" aria-hidden="true">
          <circle cx="6" cy="6" r="5.4" fill="none" stroke="var(--teal-ink)" stroke-width="0.9"/>
          <rect x="3.3" y="4" width="5.4" height="4" fill="none" stroke="var(--teal-ink)" stroke-width="0.8"/>
          <path d="M3.3 4l2.7 2.1L8.7 4" fill="none" stroke="var(--teal-ink)" stroke-width="0.8"/>
        </svg>
        hlelectricalsolutions@mailvento.com
      </li>
      <li>
        <svg class="icon" viewBox="0 0 12 12" aria-hidden="true">
          <circle cx="6" cy="6" r="5.4" fill="none" stroke="var(--teal-ink)" stroke-width="0.9"/>
        </svg>
        @hlelectricalsolutions
      </li>
    </ul>
  </div>
</section>

</body>
</html>
```